Verodex business card

Business card for sustainable investment company called "Verodex". Verodex is an exchange platform selling carbon credits between buyers and sellers. Carbon Credits are an environmental commodity for reducing global carbon emissions.

the card should obviously have our logo and the theme should be sustainability/environment mixed with a trading platform.

Contact Information for Business Card

Logo, Name, Title, Phone, Email

Colors
0054AA
0677BA
7BADD7
CADEEF
E8F1F8
0094D4
00A9DD
6FCCEA
C7EBF8
E9F6FB
00AB8E
00BBA5
67D7C9
C6EFE9
E9F9F6
59FF00
82FF00
B8FF75
E3FFCB
F4FFEA

```html
<!DOCTYPE html>
<html lang="en">
<head>
<meta charset="utf-8">
<title>Verodex business card</title>
<link href="https://fonts.googleapis.com/css2?family=Montserrat:wght@500;700&family=Roboto+Slab:wght@300&display=swap" rel="stylesheet">
<style>
  :root {
    --navy: #16294f;
    --sky: #33ade2;
    --sky-light: #6fccea;
    --stripe-grey: #d4d6da;
    --paper: #ffffff;
    --paper-shade: #eef0f2;
    --backdrop: #e7e8ea;
  }
  html, body {
    margin: 0;
    padding: 0;
    width: 1200px;
    height: 900px;
    overflow: hidden;
    background: var(--backdrop);
  }
  .canvas {
    position: relative;
    width: 1200px;
    height: 900px;
  }
  .card {
    position: absolute;
    left: 250px;
    width: 700px;
    height: 400px;
    overflow: hidden;
    box-shadow: 0 6px 18px rgba(22, 41, 79, 0.18);
  }
  .card--front { top: 35px; background: var(--navy); }
  .card--back { top: 465px; background: var(--navy); }

  .brand {
    position: absolute;
    display: flex;
    align-items: center;
    gap: 16px;
    font-family: "Montserrat", sans-serif;
    font-weight: 700;
    letter-spacing: 3px;
  }
  .brand__dot {
    border-radius: 50%;
    background: var(--sky);
  }
  .card--front .brand {
    left: 0; right: 0; top: 0; bottom: 0;
    justify-content: center;
    font-size: 64px;
    color: var(--paper);
  }
  .card--front .brand__dot { width: 52px; height: 52px; }

  .back-art { position: absolute; inset: 0; }

  .card--back .brand {
    left: 430px;
    top: 150px;
    font-size: 34px;
    color: var(--navy);
  }
  .card--back .brand__dot { width: 30px; height: 30px; }

  .holder {
    position: absolute;
    left: 88px;
    top: 48px;
    color: var(--paper);
  }
  .holder__name {
    margin: 0;
    font-family: "Montserrat", sans-serif;
    font-weight: 700;
    font-size: 24px;
    letter-spacing: 1px;
  }
  .holder__title {
    margin: 2px 0 0;
    font-family: "Montserrat", sans-serif;
    font-weight: 500;
    font-size: 17px;
    letter-spacing: 1px;
  }

  .contact {
    position: absolute;
    left: 0; top: 0;
    width: 360px; height: 400px;
  }
  .contact__text {
    position: absolute;
    margin: 0;
    font-family: "Roboto Slab", serif;
    font-weight: 300;
    font-size: 15px;
    line-height: 20px;
    color: var(--paper);
  }
  .contact__text--phone { left: 110px; top: 126px; }
  .contact__text--web { left: 124px; top: 196px; }
  .contact__text--address { left: 138px; top: 266px; }
</style>
</head>
<body>
<div class="canvas">

  <section class="card card--front">
    <div class="brand"><span class="brand__dot"></span>VERODEX</div>
  </section>

  <section class="card card--back">
    <svg class="back-art" width="700" height="400" viewBox="0 0 700 400">
      <defs>
        <linearGradient id="paperTone" x1="0" y1="0" x2="1" y2="1">
          <stop offset="0" stop-color="#f6f7f8"/>
          <stop offset="1" stop-color="#eceef0"/>
        </linearGradient>
        <linearGradient id="hexLine" x1="0" y1="0" x2="1" y2="1">
          <stop offset="0" stop-color="#2f6fc4"/>
          <stop offset="1" stop-color="#45c2ea"/>
        </linearGradient>
      </defs>

      <polygon class="accent-triangle" points="215,0 352,0 340,88" fill="var(--sky)"/>
      <polygon class="accent-triangle" points="418,400 520,400 402,318" fill="var(--sky)"/>

      <polygon class="stripe-grey" points="322,70 332,70 312,238 470,400 458,400 300,242" fill="var(--stripe-grey)"/>

      <polygon class="stripe-sky" points="352,0 366,0 340,225 526,400 512,400 326,226" fill="var(--sky)"/>
      <polygon class="stripe-white" points="366,0 374,0 348,224 534,400 526,400 340,225" fill="var(--paper)"/>
      <polygon class="stripe-navy" points="374,0 382,0 356,223 542,400 534,400 348,224" fill="var(--navy)"/>

      <g role="img" aria-label="Faint pattern of light grey triangles">
        <polygon points="382,0 700,0 700,400 542,400 356,223" fill="url(#paperTone)"/>
      </g>

      <g class="hex-chain" fill="none" stroke="url(#hexLine)" stroke-width="3">
        <line x1="60" y1="130" x2="74" y2="190"/>
        <line x1="74" y1="210" x2="88" y2="260"/>
        <line x1="88" y1="280" x2="102" y2="330"/>
      </g>

      <g class="hex hex--person">
        <polygon points="40,100 80,100 92,120 80,140 40,140 28,120" fill="url(#hexLine)"/>
        <circle cx="60" cy="114" r="5" fill="var(--paper)"/>
        <path d="M50 130 q10 -12 20 0 z" fill="var(--paper)"/>
      </g>

      <g class="hex hex--phone">
        <polygon points="56,180 92,180 104,200 92,220 56,220 44,200" fill="var(--navy)" stroke="url(#hexLine)" stroke-width="3"/>
        <path d="M66 196 q8 -6 16 0 l-2 3 h-12 z M68 199 h12 v8 h-12 z" fill="var(--paper)"/>
      </g>

      <g class="hex hex--globe">
        <polygon points="70,250 106,250 118,270 106,290 70,290 58,270" fill="var(--navy)" stroke="url(#hexLine)" stroke-width="3"/>
        <g fill="none" stroke="var(--paper)" stroke-width="1.4">
          <circle cx="88" cy="270" r="8"/>
          <ellipse cx="88" cy="270" rx="3.5" ry="8"/>
          <line x1="80" y1="270" x2="96" y2="270"/>
        </g>
      </g>

      <g class="hex hex--pin">
        <polygon points="84,320 120,320 132,340 120,360 84,360 72,340" fill="var(--navy)" stroke="url(#hexLine)" stroke-width="3"/>
        <path d="M102 350 l-6 -8 a7 7 0 1 1 12 0 z" fill="var(--paper)"/>
        <circle cx="102" cy="337" r="2.4" fill="var(--navy)"/>
      </g>
    </svg>

    <div class="holder">
      <h1 class="holder__name">MARCUS HALE</h1>
      <p class="holder__title">Founder</p>
    </div>

    <div class="contact">
      <p class="contact__text contact__text--phone">000 5550 1842<br>000 5550 1843</p>
      <p class="contact__text contact__text--web">info@verodex.com<br>www.verodex.com</p>
      <p class="contact__text contact__text--address">218, 2nd Floor,<br>Elm Road, NY 410255</p>
    </div>

    <div class="brand"><span class="brand__dot"></span>VERODEX</div>
  </section>

</div>
</body>
</html>
```